Book Cover on Entrepreneurship for Eye Doctors

Book Title: The Lens Practice Builder: How to launch with confidence
Author: Rufus Tembley, Optom, MBA, DBA, EIC
I need a Book Cover with the following descriptions:
Topic: the book topic is entrepreneurship knowledge for eye care professionals.
The book's audience: eye care professionals who you know as Opticians, who sell eyeglasses and sunglasses;
Optometrists, test eyes, fit contact lenses, and prescribe medication
Ophthalmologists, perform eye surgery
More about the audience:
1- Young eye care professionals who don’t know about entrepreneurship and those who are stuck in the 9-to-5 job;
2- This is the first book written on entrepreneurship with eye care professionals in mind.
3- Private practice owners the established business guys who are looking to grow their business;
4- Many eye care professionals are MBA holders they may have learned a little bit about entrepreneurship during their MBA studies.
Use the sample cover above and the suggestions that follow as a guide:
1- The cover should be very simple leaving an empty space somewhere to sign the book;
2- The Title and author name should use a modern font;
3- The cover should provide info about what's inside the book through illustrations, for example:
a- Gears: illustrating entrepreneur growth mindset (or anything more explicit)
b- Spectacles, sunglasses, lenses, eye drops, or any other eye care-related correction tools illustrating eye care (or anything more explicit)
c- Symbols illustrating ideas, opportunity, and profit, like money, charts, light bulbs, brain, and coins,...(or anything more explicit)
d- Entrepreneurship illustrated by Briefcase, tie, suit,... (or anything more explicit)

The rest is your creativity and imagination interplay.

Target Market(s)

Eye care professionals: Opticians, Optometrists, Ophthalmologists, Eye Care Administrators, Students in eye specialties.

Industry/Entity Type

eye care

Requirements
Must have
• 1- The cover should be very simple leaving an empty space somewhere to sign the book; 2- The Title and author name should use a modern font; 3- The cover should provide info about what's inside the book through illustrations, for example: a- Gears: illustrating entrepreneur growth mindset (or anything more explicit) b- Spectacles, sunglasses, lenses, eye drops, or any other eye care-related correction tools illustrating eye care (or anything more explicit) c- Symbols illustrating ideas, opportunity, and profit, like money, charts, light bulbs, brain, and coins,...(or anything more explicit) d- Entrepreneurship illustrated by Briefcase, tie, suit,... (or anything more explicit)

```html
<!DOCTYPE html>
<html lang="en">
<head>
<meta charset="utf-8">
<title>The Lens Practice Builder – Book Cover Wrap</title>
<link href="https://fonts.googleapis.com/css2?family=Montserrat:wght@400;500;600;700;800&display=swap" rel="stylesheet">
<style>
  :root {
    --page: #ffffff;
    --orange: #fbad3b;
    --yellow-core: #fdd835;
    --yellow-mid: #fcc331;
    --orange-edge: #f9a93a;
    --ink: #000000;
    --paper: #ffffff;
  }
  * { margin: 0; padding: 0; box-sizing: border-box; }
  html, body {
    width: 1200px; height: 1200px; overflow: hidden;
    background: var(--page);
    font-family: "Montserrat", sans-serif;
  }
  .canvas { position: relative; width: 1200px; height: 1200px; }

  .cover-wrap {
    position: absolute; left: 90px; top: 240px;
    width: 1020px; height: 719px;
    display: flex;
  }

  /* Back cover */
  .back-cover { position: relative; width: 480px; height: 100%; background: var(--ink); }
  .back-blurb-panel {
    position: absolute; left: 0; top: 0; width: 480px; height: 462px;
    background: var(--orange);
    padding: 42px 40px 0 41px;
  }
  .back-blurb p {
    font-size: 11.4px; line-height: 14.7px; color: var(--ink);
    text-align: justify; font-weight: 400;
  }
  .back-author {
    position: absolute; left: 0; top: 484px; width: 480px;
    text-align: center; color: var(--paper);
    font-size: 14px; font-weight: 500; letter-spacing: 1.4px;
  }
  .back-bio {
    position: absolute; left: 41px; top: 515px; width: 399px;
    color: var(--paper); font-size: 11.4px; line-height: 13.6px;
    text-align: justify;
  }

  /* Spine */
  .spine { position: relative; width: 60px; height: 100%; background: var(--ink); }
  .spine-title {
    position: absolute; left: 50%; top: 56px; transform: translateX(-50%);
    writing-mode: vertical-rl; white-space: nowrap;
    color: var(--paper); font-weight: 800; font-size: 21px; letter-spacing: 0.6px;
  }
  .spine-author {
    position: absolute; left: 50%; top: 510px; transform: translateX(-50%);
    writing-mode: vertical-rl; white-space: nowrap;
    color: var(--paper); font-weight: 600; font-size: 9.4px;
  }

  /* Front cover */
  .front-cover {
    position: relative; width: 480px; height: 100%;
    background: radial-gradient(ellipse 70% 62% at 50% 50%, var(--yellow-core) 0%, var(--yellow-mid) 50%, var(--orange-edge) 100%);
    text-align: center; color: var(--ink);
  }
  .title { position: absolute; left: 0; top: 68px; width: 100%; }
  .title-line { display: block; font-weight: 800; line-height: 1; }
  .title-top { font-size: 52px; letter-spacing: 13px; margin-right: -13px; }
  .title-main { font-size: 66px; letter-spacing: 1px; margin-top: 22px; }
  .title-bottom { font-size: 45px; letter-spacing: 0.5px; margin-top: 30px; }

  .glasses-art {
    position: absolute; left: 61px; top: 349px; width: 356px; height: 128px;
  }
  .subtitle {
    position: absolute; left: 0; top: 540px; width: 100%;
    font-size: 23.5px; font-weight: 500;
  }
  .front-author {
    position: absolute; left: 0; top: 650px; width: 100%;
    font-size: 17.5px; font-weight: 500;
  }
</style>
</head>
<body>
<main class="canvas">
  <section class="cover-wrap">

    <div class="back-cover">
      <div class="back-blurb-panel">
        <div class="back-blurb">
          <p>Lorem ipsum dolor sit amet, consectetuer adipiscing elit, sed diam nonummy nibh euismod tincidunt ut laoreet dolore magna aliquam erat volutpat. Ut wisi enim ad minim veniam, quis nostrud exerci tation ullamcorper suscipit lobortis nisl ut aliquip ex ea commodo consequat. Duis autem vel eum iriure dolor in hendrerit in vulputate velit esse molestie consequat, vel illum dolore eu feugiat nulla facilisis at vero eros et accumsan et iusto odio dignissim qui blandit praesent luptatum zzril delenit augue duis dolore te feugait nulla facilisi.</p>
          <p>Lorem ipsum dolor sit amet, cons ectetuer adipiscing elit, sed diam nonummy nibh euismod tincidunt ut laoreet dolore magna aliquam erat volutpat. Ut wisi enim ad minim veniam, quis nostrud exerci tation ullamcorper suscipit lobortis nisl ut aliquip ex ea commodo consequat.</p>
          <p>Lorem ipsum dolor sit amet, consectetuer adipiscing elit, sed diam nonummy nibh euismod tincidunt ut laoreet dolore magna aliquam erat volutpat. Ut wisi enim ad minim veniam, quis nostrud exerci tation ullamcorper suscipit lobortis nisl ut aliquip ex ea commodo consequat. Duis autem vel eum iriure dolor in hendrerit in vulputate velit esse molestie consequat, vel illum dolore eu feugiat nulla facilisis at vero eros et accumsan et iusto odio dignissim qui blandit praesent luptatum zzril delenit augue duis dolore te feugait nulla facilisi.</p>
          <p>Lorem ipsum dolor sit amet, cons ectetuer adipiscing elit, sed diam nonummy nibh euismod tincidunt ut laoreet dolore magna aliquam erat volutpat. Ut wisi enim ad minim veniam, quis nostrud exerci tation ullamcorper suscipit lobortis nisl ut aliquip ex ea commodo consequat.</p>
        </div>
      </div>
      <p class="back-author">Rufus Tembley, Optom, MBA, DBA, EIC</p>
      <p class="back-bio">Lorem ipsum dolor sit amet, consectetuer adipiscing elit, sed diam nonummy nibh euismod tincidunt ut laoreet dolore magna aliquam erat volutpat. Ut wisi enim ad minim veniam, quis nostrud exerci tation ullamcorper suscipit lobortis nisl ut aliquip ex ea commodo consequat. Duis autem vel eum iriure dolor in hendrerit in vulputate velit esse molestie consequat, vel illum dolore eu feugiat nulla facilisis at vero eros et accumsan et iusto odio dignissim qui blandit praesent luptatum zzril delenit augue duis dolore te feugait nulla facilisi.</p>
    </div>

    <div class="spine">
      <span class="spine-title">THE LENS PRACTICE BUILDER</span>
      <span class="spine-author">Rufus Tembley, Optom, MBA, DBA, EIC</span>
    </div>

    <div class="front-cover">
      <h1 class="title">
        <span class="title-line title-top">THE LENS</span>
        <span class="title-line title-main">PRACTICE</span>
        <span class="title-line title-bottom">BUILDER</span>
      </h1>
      <svg class="glasses-art" role="img" aria-label="Illustration of black-framed eyeglasses with yellow lenses" viewBox="0 0 356 128">
        <defs>
          <radialGradient id="glassesTone" cx="50%" cy="45%" r="60%">
            <stop offset="0%" stop-color="#3a3320"/>
            <stop offset="100%" stop-color="#1a1a1a"/>
          </radialGradient>
        </defs>
        <rect x="0" y="0" width="356" height="128" rx="40" fill="url(#glassesTone)" opacity="0.85"/>
      </svg>
      <p class="subtitle">How to launch with confidence</p>
      <p class="front-author">Rufus Tembley, Optom, MBA, DBA, EIC</p>
    </div>

  </section>
</main>
</body>
</html>
```